Business Card and Letterhead for Pimlu - modern real estate business

I need a double sided business card design for Pimlu. Please see business card brief here https://files.trelvonadocs.com/sheet/r/7QzTmWbaXLJnoPEd-kRyUgFhHsstbvCe2qfoMxDa_pz/view?mode=shared

Please feel free to design the business cards however you feel best. I am happy to give some creative freedoms and then provide feedback from there.

Please then also create a letterhead to match the business card design

Colors

Designer to choose colors to be used in the design.

Requirements
Must have
• Must be a modern, elegant business card which looks very professional

```html
<!DOCTYPE html>
<html lang="en">
<head>
<meta charset="utf-8">
<title>Pimlu Letterhead</title>
<link href="https://fonts.googleapis.com/css2?family=Montserrat:wght@400;500;700;800&family=Open+Sans:wght@400&display=swap" rel="stylesheet">
<style>
  :root {
    --backdrop: #a5b7bc;
    --paper: #ffffff;
    --brand-red: #e0121b;
    --ink: #1f1f1f;
    --body-ink: #333333;
    --signature-tone: #d9dde0;
  }
  * { margin: 0; padding: 0; box-sizing: border-box; }
  html, body {
    width: 1200px; height: 900px; overflow: hidden;
    background: var(--backdrop);
  }
  .canvas { position: relative; width: 1200px; height: 900px; }
  .letterhead {
    position: absolute; left: 293px; top: 57px;
    width: 614px; height: 785px;
    background: var(--paper);
    box-shadow: 0 2px 6px rgba(0,0,0,0.18);
  }
  .letterhead__bar {
    position: absolute; left: 0; right: 0; bottom: 0; height: 6px;
    background: var(--brand-red);
  }
  .sender {
    position: absolute; left: 38px; top: 27px;
    font-family: "Montserrat", sans-serif; font-size: 10px; line-height: 12px;
    color: var(--ink);
  }
  .sender__contacts { margin-top: 2px; list-style: none; }
  .sender__contacts li { display: flex; align-items: center; gap: 4px; line-height: 12px; }
  .sender__contacts svg { width: 9px; height: 9px; flex: none; }
  .brand-name {
    position: absolute; right: 38px; top: 38px;
    font-family: "Montserrat", sans-serif; font-weight: 800;
    font-size: 36px; line-height: 36px; letter-spacing: 1px;
    color: var(--brand-red);
  }
  .letter {
    position: absolute; left: 68px; top: 218px; width: 475px;
    font-family: "Open Sans", sans-serif; font-size: 10px;
    color: var(--body-ink);
  }
  .letter__date { line-height: 14px; margin-bottom: 36px; }
  .letter__para { margin-bottom: 2px; }
  .letter__para + .letter__para { margin-top: 2px; }
  .letter__para span {
    display: block; line-height: 22px; white-space: nowrap; overflow: hidden;
  }
  .letter__para--gap { margin-top: 6px !important; }
  .signoff {
    position: absolute; left: 424px; top: 553px;
    font-family: "Open Sans", sans-serif; font-size: 10px; line-height: 12px;
    color: var(--ink);
  }
  .signoff__signature {
    width: 122px; height: 38px; margin-bottom: 3px;
    background: linear-gradient(90deg, var(--signature-tone), #eceef0);
    border-radius: 3px;
  }
  .registration {
    position: absolute; left: 0; right: 0; top: 750px;
    text-align: center;
    font-family: "Montserrat", sans-serif; font-size: 10px; line-height: 12px;
    color: var(--ink);
  }
</style>
</head>
<body>
<main class="canvas">
  <article class="letterhead">
    <header>
      <address class="sender" style="font-style:normal">
        <div>PO Box 3917</div>
        <div>Larkvale NSW 2791</div>
        <ul class="sender__contacts">
          <li>
            <svg viewBox="0 0 10 10" aria-hidden="true"><circle cx="5" cy="5" r="5" fill="var(--brand-red)"/><path d="M3.2 2.6l1 1-.5.7c.4.8.9 1.3 1.6 1.6l.7-.5 1 1-.6.8C4.7 7 3 5.3 2.5 3.2z" fill="#fff"/></svg>
            02 4318 2957
          </li>
          <li>
            <svg viewBox="0 0 10 10" aria-hidden="true"><circle cx="5" cy="5" r="5" fill="var(--brand-red)"/><rect x="2.4" y="3.2" width="5.2" height="3.6" fill="#fff"/><path d="M2.4 3.2L5 5.2l2.6-2" stroke="var(--brand-red)" stroke-width=".6" fill="none"/></svg>
            info@pimlu.com
          </li>
          <li>
            <svg viewBox="0 0 10 10" aria-hidden="true"><circle cx="5" cy="5" r="5" fill="var(--brand-red)"/><circle cx="5" cy="5" r="2.6" fill="none" stroke="#fff" stroke-width=".7"/><path d="M2.4 5h5.2M5 2.4v5.2" stroke="#fff" stroke-width=".6"/></svg>
            www.pimlu.com
          </li>
        </ul>
      </address>
      <div class="brand-name">PIMLU</div>
    </header>

    <section class="letter">
      <p class="letter__date">Date, 10 September, 2020</p>
      <p class="letter__para">
        <span>This is a sample letter that has been placed to demonstrate typing remat (Your Company). letterhead</span>
        <span>design. When positioned properly, it will serve to work in harmony with all other elements letterhead.</span>
        <span>This letterhead design is meant to project an image</span>
      </p>
      <p class="letter__para">
        <span>This letterhead design is meant project an image of professionalism reliability. By using simple aligen</span>
        <span>we have created a very spacious feeling. The simplicity suggest&nbsp; rengththe spaciousnes contributes h</span>
        <span>aesthetics the layout. These basic qualities along with the (Your Company)</span>
      </p>
      <p class="letter__para letter__para--gap">
        <span>look and helps reinforce the (Your Company) brand. letterhead design is meant to project an image p</span>
        <span>design. When positioned properly, it will serve to work in harmony all the other elements letterhead.</span>
        <span>sionalism and reliability.</span>
      </p>
      <p class="letter__para letter__para--gap">
        <span>This letterhead design is based on the (Form of your logo) form (Your Company) logo. Each stationery</span>
        <span>we have created a very spacious feeling. The simplicity suggests strength the spaciousnes contribute</span>
        <span>part of the (Form of your logo).</span>
      </p>
    </section>

    <div class="signoff">
      <div class="signoff__signature" role="img" aria-label="Handwritten signature of Marten Hollis"></div>
      <div>Marten Hollis</div>
      <div>Manager</div>
    </div>

    <footer class="registration">
      <div>ABN: 41 827 309 164</div>
      <div>Lic No. 20473815</div>
    </footer>
    <div class="letterhead__bar"></div>
  </article>
</main>
</body>
</html>
```